business card deign

Logo needs the following on it.
1. attached logo
2. Tagline - "If it keeps a drink cold or the party going...we do it!"
3. Name- Dalton Pikes, Founder and CPO
4. Address - 412 E. Carver Avenue, Ste 2207, Tampa, FL. 33917
5. Phone - 555.318.4726

```html
<!DOCTYPE html>
<html lang="en">
<head>
<meta charset="utf-8">
<title>Hopwell Business Card</title>
<link href="https://fonts.googleapis.com/css2?family=Montserrat:wght@400;500;700&display=swap" rel="stylesheet">
<style>
  :root {
    --backdrop: #3b332f;
    --card-white: #ffffff;
    --card-black: #1b1b1b;
    --ink: #161616;
    --ink-soft: #333333;
    --rule: #222222;
    --emboss: #2c2c2c;
  }
  * { margin: 0; padding: 0; box-sizing: border-box; }
  html, body {
    width: 1200px; height: 786px; overflow: hidden;
    background: var(--backdrop);
    font-family: "Montserrat", sans-serif;
  }
  .stage { position: relative; width: 1200px; height: 786px; }
  .card {
    position: absolute;
    width: 525px; height: 300px;
    box-shadow: 0 10px 30px rgba(0,0,0,0.45);
  }
  .card--front { left: 55px; top: 300px; background: var(--card-white); color: var(--ink); }
  .card--back { left: 620px; top: 186px; background: var(--card-black); }

  .brand-name {
    position: absolute; left: 30px; top: 132px; width: 190px;
    text-align: center;
    font-weight: 500; font-size: 20px; letter-spacing: 0;
    color: var(--ink);
  }
  .divider {
    position: absolute; left: 240px; top: 55px;
    width: 1.5px; height: 150px; background: var(--rule);
  }
  .details { position: absolute; left: 258px; top: 50px; }
  .details__name { font-weight: 700; font-size: 17px; line-height: 1.1; }
  .details__title { font-size: 10.5px; color: var(--ink-soft); margin-top: 2px; }
  .details__address { font-size: 10.5px; color: var(--ink-soft); line-height: 1.35; margin-top: 14px; padding-left: 22px; }
  .contact-list { list-style: none; margin-top: 12px; }
  .contact-list li {
    display: flex; align-items: center; gap: 8px;
    font-size: 11.5px; color: var(--ink-soft); line-height: 1; margin-bottom: 8px;
  }
  .contact-list svg { width: 11px; height: 11px; flex: none; }
  .icon--solid { fill: var(--ink); }
  .icon--line { fill: none; stroke: var(--ink); stroke-width: 2.4; }
  .tagline {
    position: absolute; left: 0; right: 0; bottom: 38px;
    text-align: center; font-size: 12.5px; font-weight: 500; color: var(--ink);
  }
  .back-name {
    position: absolute; left: 0; right: 0; top: 134px;
    text-align: center;
    font-weight: 500; font-size: 24px; letter-spacing: 0;
    color: var(--emboss);
  }
</style>
</head>
<body>
<main class="stage">
  <section class="card card--front" aria-label="Front of business card">
    <p class="brand-name">Hopwell</p>
    <div class="divider"></div>
    <div class="details">
      <p class="details__name">Dalton Pikes</p>
      <p class="details__title">Founder and CPO</p>
      <p class="details__address">412 E. Carver Avenue, Ste 2207,<br>Tampa, FL. 33917</p>
      <ul class="contact-list">
        <li>
          <svg class="icon--solid" viewBox="0 0 24 24" aria-hidden="true"><path d="M6.6 10.8a15.1 15.1 0 0 0 6.6 6.6l2.2-2.2a1 1 0 0 1 1-.25 11.4 11.4 0 0 0 3.6.57 1 1 0 0 1 1 1V20a1 1 0 0 1-1 1A17 17 0 0 1 3 4a1 1 0 0 1 1-1h3.5a1 1 0 0 1 1 1c0 1.25.2 2.45.57 3.57a1 1 0 0 1-.25 1z"/></svg>
          555.318.4726
        </li>
        <li>
          <svg class="icon--line" viewBox="0 0 24 24" aria-hidden="true"><rect x="2.5" y="5" width="19" height="14"/><path d="M2.5 5l9.5 8 9.5-8"/></svg>
          info@hopwell.com
        </li>
        <li>
          <svg class="icon--line" viewBox="0 0 24 24" aria-hidden="true"><circle cx="12" cy="12" r="9.5"/><path d="M2.5 12h19M12 2.5c3 3 3 16 0 19M12 2.5c-3 3-3 16 0 19"/></svg>
          www.hopwell.com
        </li>
      </ul>
    </div>
    <p class="tagline">If it keeps a drink cold or the party going...we do it</p>
  </section>

  <section class="card card--back" aria-label="Back of business card">
    <p class="back-name">Hopwell</p>
  </section>
</main>
</body>
</html>
```